Company brochure for our unique consulting business

We are a small consulting business offering a unique set of services to our clients.. In simple terms we are a business improvement consultancy helping our clients get the best out of their businesses. We work with clients across multiple sectors and deliver a variety of services. We want to put together a brochure to cover these main themes:1. Who we are2. What we do3. The type of people we employ4. The sectors we work inWhile the brochure needs to have a certain corporate feel to it, we don't want it to be "boring" or "stiff". We would like it to have a slightly "friendly" or "informal" feel to it, to reflect the type of organisation we are.We have a company website http://brevalconsultingpartners.net , however we do not want to directly replicate the content or feel as we recognise it needs updating.We would like the brochure to be A4 portrait format. We anticipate requiring 12 sides (including covers) but we are happy to be guided on this based on the content we have provided.The attached ppt file gives the detail of the content to be included and also shows the proposed pagination. For the front cover we would like to try 2 versions, one with the BCP logo and one with the Breval Consulting Partners logo (a file of both is attached)One of the most important pages will be the "Our Services" page. We would like this to cover the centre fold. In the ppt file we have shown an example layout, but this is where we need most help - we are clearly not graphic designers! This page will be the most used page in sales meetings etc.Also attached is the following:1. file for our BrevalConsulting Partners company logo.2. File for our BCP company logo3. Files for Derek's signatures (for under photos) - Owen's to follow4. Photo of Derek & Owen (person in purple shirt to be cropped out)Thank you and really excited to see what everyone comes back with.Derek & Owen

Target Market(s)

Very broad - Manufacturing, Healthcare, Hospitality

Industry/Entity Type

Management Consulting

Font styles to use
Other font styles liked:
• We use Swiss721, but happy to be guided by designer

Colors
3276b5
85abd2
0355a3
333333
5c5c5c
9d9d9d
d9d9d9

Requirements
Must have
• Corporate feel
Nice to have
• Slightly friendly feel
• Our standard "blue" is (CORRECTION) - R55 G96 B146 #376092 and our standard grey is R197 G178, B179 - #B3B2B2, which we would like to keep, but other colours we are happy to be guided on. Brand guidelines attached.

```html
<!DOCTYPE html>
<html lang="en">
<head>
<meta charset="utf-8">
<title>Breval Consulting Partners – Brochure</title>
<link href="https://fonts.googleapis.com/css2?family=Arimo:ital,wght@0,400;0,700;1,400;1,700&display=swap" rel="stylesheet">
<style>
  :root{
    --brand-blue:#376092;
    --deep-blue:#0355a3;
    --ink:#333333;
    --mid-grey:#5c5c5c;
    --soft-grey:#9d9d9d;
    --pale-grey:#d9d9d9;
    --brand-grey:#b3b2b2;
    --backdrop:#7b7b7b;
    --paper:#ffffff;
  }
  *{box-sizing:border-box;margin:0;padding:0}
  html,body{width:1200px;height:1200px;overflow:hidden}
  body{background:var(--backdrop);font-family:"Arimo",Arial,sans-serif;color:var(--mid-grey);position:relative}

  .page{position:absolute;background:var(--paper);overflow:hidden;box-shadow:0 6px 18px rgba(0,0,0,.35)}
  .spread-left{left:30px;top:30px;width:420px;height:594px}
  .spread-right{left:450px;top:30px;width:420px;height:594px}
  .spread-left::after{content:"";position:absolute;right:0;top:0;width:70px;height:100%;background:linear-gradient(90deg,rgba(0,0,0,0),rgba(0,0,0,.16))}
  .spread-right::before{content:"";position:absolute;left:0;top:0;width:60px;height:100%;background:linear-gradient(90deg,rgba(0,0,0,.18),rgba(0,0,0,0));z-index:3}

  /* section header band */
  .section-band{position:absolute;height:40px;background:var(--brand-blue);color:#fff;font-weight:700;font-style:italic;font-size:20px;line-height:40px;letter-spacing:.5px;white-space:nowrap}
  .section-band.values{left:0;top:44px;width:160px;padding-left:16px}
  .section-band.story{right:0;top:20px;width:150px;padding-left:16px}
  .band-stripes{position:absolute}
  .band-stripes.values{left:166px;top:44px}
  .band-stripes.story{left:196px;top:20px}

  /* values list */
  .value{position:absolute;font-size:10.5px;font-style:italic;line-height:1.35;color:var(--mid-grey);width:230px}
  .value strong{font-weight:700;color:var(--ink);letter-spacing:.2px}
  .value::after{content:"";position:absolute;bottom:-7px;height:2px;width:120px;background:var(--brand-blue)}
  .value.text-left{text-align:left}
  .value.text-left::after{left:0}
  .value.text-right{text-align:right}
  .value.text-right::after{right:0}
  .value-icon{position:absolute;width:58px;height:58px}

  .folio{position:absolute;bottom:22px;font-size:11px;font-weight:700;color:var(--brand-blue);letter-spacing:.5px}
  .folio-left{right:160px}

  /* wordmark */
  .wordmark{position:absolute;font-weight:700;color:var(--ink);line-height:1;letter-spacing:-.3px;white-space:nowrap}
  .wordmark.inside{left:34px;top:74px;font-size:21px}
  .wordmark.cover{left:140px;top:68px;font-size:22px}

  .intro{position:absolute;left:170px;top:128px;width:236px;font-size:10.5px;font-style:italic;line-height:1.4}
  .photo{position:absolute}
  .partners-photo{left:168px;top:190px;width:238px;height:160px;background:linear-gradient(160deg,#f1ece4 0%,#d9dde2 45%,#7da3cf 100%)}
  .signature{position:absolute;left:270px;top:360px;width:110px;height:24px;background:linear-gradient(90deg,#e6e6e6,#f4f4f4)}
  .signatory{position:absolute;left:270px;top:390px;font-size:11px;line-height:1.3}
  .signatory .name{font-weight:700;color:var(--ink)}
  .signatory .role{font-style:italic;font-size:9.5px}
  .story-body{position:absolute;left:214px;top:436px;width:190px;font-size:10.5px;font-style:italic;line-height:1.4}
  .tiles{position:absolute;left:20px;top:150px}
  .folio-right{left:214px}

  /* cover */
  .cover{left:790px;top:600px;width:380px;height:537px}
  .cover-band{position:absolute;left:196px;right:0;top:136px;height:12px;background:var(--brand-blue)}
  .globe-photo{left:0;top:160px;width:380px;height:230px;background:radial-gradient(ellipse 70% 80% at 62% 40%,#dfe6ee 0%,#8ea4b8 40%,#51677d 80%,#3f5468 100%)}
  .tagline{position:absolute;left:40px;top:352px;width:240px;height:28px;background:var(--mid-grey);color:#fff;font-style:italic;font-size:16px;line-height:28px;padding-left:16px;border-radius:2px;z-index:2;white-space:nowrap}
  .tagline strong{font-weight:700}
  .cover-tab{position:absolute;z-index:1}
  .cover-tab.down{left:36px;top:0}
  .cover-tab.up{left:270px;top:318px;z-index:3}
</style>
</head>
<body>

<!-- Inside spread: values page -->
<section class="page spread-left" aria-label="Our values">
  <div class="section-band values">OUR VALUES</div>
  <svg class="band-stripes values" width="60" height="40" viewBox="0 0 60 40">
    <g fill="var(--brand-blue)"><rect x="2" y="0" width="7" height="40"/><rect x="14" y="0" width="7" height="40"/><rect x="26" y="0" width="7" height="40"/><rect x="38" y="0" width="7" height="40"/></g>
  </svg>

  <p class="value text-left" style="left:24px;top:110px">Be <strong>TRUSTED</strong> by our team and clients, so that our opinions are sought and our recommendations valued.</p>
  <svg class="value-icon" style="left:320px;top:118px" viewBox="0 0 58 58" aria-hidden="true">
    <rect width="58" height="58" rx="10" fill="var(--brand-blue)"/>
    <path d="M14 26a15 12 0 0 1 30 0z" fill="#fff"/><line x1="29" y1="26" x2="29" y2="34" stroke="#fff" stroke-width="2"/>
    <circle cx="22" cy="40" r="4" fill="#fff"/><circle cx="36" cy="40" r="4" fill="#fff"/><circle cx="29" cy="44" r="4" fill="#fff"/>
  </svg>

  <p class="value text-right" style="left:76px;top:190px">Have a tight knit relationship with our clients, so we are seen as a <strong>PARTNER</strong> and not just supplier.</p>
  <svg class="value-icon" style="left:18px;top:194px" viewBox="0 0 58 58" aria-hidden="true">
    <rect width="58" height="58" rx="10" fill="var(--brand-blue)"/>
    <circle cx="22" cy="22" r="6" fill="#fff"/><circle cx="36" cy="22" r="6" fill="#fff"/>
    <path d="M12 42a10 10 0 0 1 20 0zM26 42a10 10 0 0 1 20 0z" fill="#fff"/>
  </svg>

  <p class="value text-left" style="left:90px;top:270px">Be focused on return-on-investment, but predominantly, always deliver <strong>GREAT VALUE.</strong></p>
  <svg class="value-icon" style="left:18px;top:272px" viewBox="0 0 58 58" aria-hidden="true">
    <rect width="58" height="58" rx="10" fill="var(--brand-blue)"/>
    <g fill="#fff"><rect x="14" y="34" width="6" height="12"/><rect x="23" y="28" width="6" height="18"/><rect x="32" y="22" width="6" height="24"/></g>
    <path d="M13 28 L26 18 L32 22 L44 12" stroke="#fff" stroke-width="2.5" fill="none"/><circle cx="44" cy="42" r="5" fill="#fff"/>
  </svg>

  <p class="value text-right" style="left:76px;top:350px"><strong>DEVELOP &amp; INVEST IN</strong> our own people to continually stay one step ahead.</p>
  <svg class="value-icon" style="left:320px;top:346px" viewBox="0 0 58 58" aria-hidden="true">
    <rect width="58" height="58" rx="10" fill="var(--brand-blue)"/>
    <rect x="13" y="13" width="32" height="22" rx="2" fill="none" stroke="#fff" stroke-width="2.5"/>
    <path d="M17 30 L23 22 L28 27 L34 18 L40 24" stroke="#fff" stroke-width="2" fill="none"/>
    <path d="M29 35 L22 48 M29 35 L36 48 M29 35 V46" stroke="#fff" stroke-width="2.5"/>
  </svg>

  <p class="value text-left" style="left:90px;top:430px">Work relentlessly to deliver results for our clients, but ensure we collectively <strong>ENJOY THE JOURNEY.</strong></p>
  <svg class="value-icon" style="left:18px;top:430px" viewBox="0 0 58 58" aria-hidden="true">
    <rect width="58" height="58" rx="10" fill="var(--brand-blue)"/>
    <circle cx="29" cy="29" r="14" fill="none" stroke="#fff" stroke-width="2.5"/>
    <ellipse cx="29" cy="29" rx="6" ry="14" fill="none" stroke="#fff" stroke-width="2"/>
    <line x1="15" y1="29" x2="43" y2="29" stroke="#fff" stroke-width="2"/>
  </svg>

  <p class="value text-right" style="left:76px;top:505px">Take <strong>SOCIAL RESPONSIBILITY</strong> seriously by supporting other worthwhile organisations.</p>
  <svg class="value-icon" style="left:320px;top:500px" viewBox="0 0 58 58" aria-hidden="true">
    <rect width="58" height="58" rx="10" fill="var(--brand-blue)"/>
    <path d="M16 26a14 14 0 0 1 24-8" stroke="#fff" stroke-width="2.5" fill="none"/><path d="M40 12v7h-7" stroke="#fff" stroke-width="2.5" fill="none"/>
    <path d="M42 32a14 14 0 0 1-24 8" stroke="#fff" stroke-width="2.5" fill="none"/><path d="M18 46v-7h7" stroke="#fff" stroke-width="2.5" fill="none"/>
    <circle cx="29" cy="29" r="5" fill="#fff"/>
  </svg>

  <p class="folio folio-left">BCP</p>
</section>

<!-- Inside spread: story page -->
<section class="page spread-right" aria-label="Our story">
  <svg class="band-stripes story" width="60" height="40" viewBox="0 0 60 40">
    <g fill="var(--brand-blue)"><rect x="14" y="0" width="7" height="40"/><rect x="26" y="0" width="7" height="40"/><rect x="38" y="0" width="7" height="40"/><rect x="50" y="0" width="7" height="40"/></g>
  </svg>
  <div class="section-band story">OUR STORY</div>

  <p class="wordmark inside">Breval Consulting<br>Partners</p>

  <p class="intro">At BCP we constantly strive to deliver the best possible value for our clients. Importantly we recognize, it's our clients that define value, not us.</p>

  <svg class="tiles" width="150" height="380" viewBox="0 0 150 380" aria-hidden="true">
    <rect x="0" y="10" width="110" height="110" rx="14" fill="var(--mid-grey)"/>
    <path d="M30 150 H110 L140 190 L110 230 H30 Q20 230 20 220 V160 Q20 150 30 150z" fill="var(--brand-blue)" stroke="#fff" stroke-width="4"/>
    <rect x="40" y="250" width="100" height="110" rx="14" fill="var(--soft-grey)"/>
  </svg>

  <div class="photo partners-photo" role="img" aria-label="Photo of the two partners smiling at a meeting table"></div>
  <div class="signature" role="img" aria-label="Handwritten signature of Derek Halloway"></div>
  <p class="signatory"><span class="name">Derek Halloway</span><br><span class="role">Partner</span></p>

  <p class="story-body">We have worked with a wide range of clients, from Norvane Motors and our local hospitals to small organisations that run their own family businesses.</p>

  <p class="folio folio-right">BCP</p>
</section>

<!-- Front cover -->
<section class="page cover" aria-label="Front cover">
  <svg class="cover-tab down" width="104" height="200" viewBox="0 0 104 200" aria-hidden="true">
    <path d="M4 -4 H100 V150 L52 196 L4 150z" fill="var(--soft-grey)" stroke="#fff" stroke-width="5"/>
  </svg>

  <p class="wordmark cover">Breval Consulting<br>Partners</p>
  <div class="cover-band"></div>

  <div class="photo globe-photo" role="img" aria-label="Photo of a light bulb with a glowing globe inside, lying on a grey surface"></div>

  <p class="tagline">helping businesses <strong>evolve</strong></p>

  <svg class="cover-tab up" width="90" height="200" viewBox="0 0 90 200" aria-hidden="true">
    <path d="M4 56 L45 4 L86 56 V190 Q86 196 80 196 H10 Q4 196 4 190z" fill="var(--brand-blue)" stroke="#fff" stroke-width="5"/>
  </svg>
</section>

</body>
</html>
```